Home Remodeling company needs a business card design

we need a business card design for home remodeling company in hamilton county, indiana USA. we offers a wide range of construction services including whole house renovations, Design and Build Basements and Kitchen and Bathroom Remodeling . we would like to see designs for both site of business card that use the same color of the company logo and also including all information below :
1- Karim Feltous CEO / General Contractor
2- all company contacts Telephone numbers ( 1-888-DULOM-47 ) ( 317-555-0193) email address ( info@dulomhome.com) website ( www.dulomhome.com ) and social media logos (Facebook- twitter- google plus )
3- company logo
4- licensed . insured . bonded

```html
<!DOCTYPE html>
<html lang="en">
<head>
<meta charset="UTF-8">
<title>Dulom Home Remodeling – Business Card</title>
<link href="https://fonts.googleapis.com/css2?family=Open+Sans:wght@400;600;700;800&display=swap" rel="stylesheet">
<style>
  :root {
    --backdrop: #d6d6d6;
    --card-black: #0d0d0d;
    --card-edge: #1c1c1c;
    --ink-white: #ffffff;
    --ink-grey: #3a3a3a;
    --ink-soft: #bdbdbd;
    --accent-red: #d0313a;
    --rule: #4a4a4a;
  }
  * { margin: 0; padding: 0; box-sizing: border-box; }
  html, body {
    width: 1200px; height: 900px; overflow: hidden;
    background: var(--backdrop);
    font-family: "Open Sans", Arial, sans-serif;
  }
  .sheet {
    width: 1200px; height: 900px;
    display: flex; flex-direction: column; align-items: center; justify-content: center;
    gap: 50px;
  }
  .card {
    position: relative;
    width: 665px; height: 380px;
    background: radial-gradient(ellipse at 55% 35%, var(--card-edge), var(--card-black) 75%);
    box-shadow: 0 6px 18px rgba(0,0,0,.28);
    color: var(--ink-white);
    overflow: hidden;
  }

  /* Front side */
  .card-front .brand {
    position: absolute; top: 95px; left: 0; right: 0;
    text-align: center;
  }
  .brand-name {
    font-weight: 800; font-size: 64px; letter-spacing: 2px; line-height: 1;
    color: var(--ink-white);
  }
  .brand-tagline {
    margin-top: 4px;
    font-weight: 600; font-size: 17px; letter-spacing: 7px;
    color: var(--ink-white);
  }
  .credentials {
    position: absolute; top: 250px; left: 0; right: 0;
    display: flex; align-items: center; gap: 16px;
  }
  .credentials .rule { flex: 1; height: 1px; background: var(--ink-soft); opacity: .7; }
  .credentials span {
    font-weight: 600; font-size: 18px; color: var(--ink-white); white-space: nowrap;
  }

  /* Back side */
  .card-back .brand {
    position: absolute; top: 48px; right: 50px;
    text-align: center;
  }
  .card-back .brand-name { color: var(--ink-grey); font-size: 58px; }
  .card-back .brand-tagline { color: var(--ink-grey); font-size: 15px; letter-spacing: 6px; }

  .person { position: absolute; top: 145px; left: 42px; }
  .person-name { color: var(--accent-red); font-weight: 600; font-size: 19px; }
  .person-title { color: var(--ink-white); font-size: 15px; margin-top: 2px; }
  .divider {
    position: absolute; top: 208px; left: 42px; right: 50px;
    height: 1px; background: var(--rule);
  }
  .social { position: absolute; top: 232px; left: 42px; display: flex; gap: 12px; }
  .social-icon {
    width: 30px; height: 30px; border-radius: 50%; background: var(--ink-white);
    display: flex; align-items: center; justify-content: center;
  }
  .social-icon svg { width: 16px; height: 16px; }

  .contacts {
    position: absolute; right: 50px; bottom: 38px;
    list-style: none; text-align: right;
  }
  .contacts li {
    display: flex; justify-content: flex-end; align-items: center; gap: 12px;
    font-size: 16px; line-height: 27px; color: var(--ink-white);
  }
  .contacts svg { width: 14px; height: 14px; flex: none; }
</style>
</head>
<body>
<main class="sheet">

  <section class="card card-front" aria-label="Card front">
    <div class="brand">
      <div class="brand-name">DULOM</div>
      <div class="brand-tagline">HOME REMODELING</div>
    </div>
    <div class="credentials">
      <div class="rule"></div>
      <span>Licensed . Insured . Bonded</span>
      <div class="rule"></div>
    </div>
  </section>

  <section class="card card-back" aria-label="Card back">
    <div class="brand">
      <div class="brand-name">DULOM</div>
      <div class="brand-tagline">HOME REMODELING</div>
    </div>

    <div class="person">
      <div class="person-name">Karim Feltous</div>
      <div class="person-title">CEO / General Contractor</div>
    </div>
    <div class="divider"></div>

    <div class="social" aria-label="Social media">
      <div class="social-icon">
        <svg viewBox="0 0 16 16" aria-hidden="true"><g fill="#0d0d0d"><circle cx="12" cy="3.5" r="2.2"/><circle cx="4" cy="8" r="2.2"/><circle cx="12" cy="12.5" r="2.2"/></g><path d="M12 3.5L4 8l8 4.5" fill="none" stroke="#0d0d0d" stroke-width="1.3"/></svg>
      </div>
      <div class="social-icon">
        <svg viewBox="0 0 16 16" aria-hidden="true"><path d="M2 3h12v8H7l-3 3v-3H2z" fill="#0d0d0d"/></svg>
      </div>
      <div class="social-icon">
        <svg viewBox="0 0 16 16" aria-hidden="true"><g fill="none" stroke="#0d0d0d" stroke-width="1.4"><circle cx="8" cy="8" r="6"/><ellipse cx="8" cy="8" rx="2.6" ry="6"/><path d="M2 8h12"/></g></svg>
      </div>
    </div>

    <ul class="contacts">
      <li>1-888-DULOM-47
        <svg viewBox="0 0 16 16" aria-hidden="true"><path fill="#d0313a" d="M3.5 1.5l2.5 0 1 3.5-1.7 1.2a9 9 0 0 0 4.5 4.5L11 9l3.5 1v2.5c0 1-1 2-2 2A11 11 0 0 1 1.5 3.5c0-1 1-2 2-2z"/></svg>
      </li>
      <li>317-555-0193
        <svg viewBox="0 0 16 16" aria-hidden="true"><path fill="#d0313a" d="M3.5 1.5l2.5 0 1 3.5-1.7 1.2a9 9 0 0 0 4.5 4.5L11 9l3.5 1v2.5c0 1-1 2-2 2A11 11 0 0 1 1.5 3.5c0-1 1-2 2-2z"/></svg>
      </li>
      <li>info@dulomhome.com
        <svg viewBox="0 0 16 16" aria-hidden="true"><rect x="1" y="3" width="14" height="10" fill="#d0313a"/><path d="M1 3l7 6 7-6" fill="none" stroke="#0d0d0d" stroke-width="1.3"/></svg>
      </li>
      <li>www.dulomhome.com
        <svg viewBox="0 0 16 16" aria-hidden="true"><g fill="none" stroke="#d0313a" stroke-width="2"><rect x="1.5" y="7" width="8" height="5" rx="2.5" transform="rotate(-45 5.5 9.5)"/><rect x="6.5" y="4" width="8" height="5" rx="2.5" transform="rotate(-45 10.5 6.5)"/></g></svg>
      </li>
    </ul>
  </section>

</main>
</body>
</html>
```